Business Card Design Project for a Restaurant/Wine Bar

New, fresh business card design for Brevenna Wine Bar & Restaurant, Bandon, Oregon. We are an established restaurant on the Oregon coast featuring "Italian coastal cuisine."

"Brevenna" means bay leaf in Italian. We aren't sure if we would like our logo on the card or not, but if you have something interesting that uses it, then please do so. The basic information is essential - full restaurant name, address, phone and website (do not use www). The font on our menu and wine list may give you some sort of an idea of our style.

One-sided card needed as we often use the backside to write down various types of info for customers.
Updates

After seeing a few submissions, we would like to see what designers can come up with-using the logo, just the leaf, or none at all. Sky is the limit as long as our full restaurant name, address, phone and website (please leave out www) are there. Please contact us if questions!

I appreciate all of your designs! Our deadline is next week, but I will continue to give feedback on designs as I can. This is our busiest season, so my co-owner/chef/husband, won't have time to look at the designs for awhile. When he does, we can make our decision.

cheers,
Maren

Target Market(s)

Fine dining/wine crowd. Would like something simple and elegant, but not pretentious or stuffy. Brevenna means bay laurel (bay leaf) in Italian (please see our logo).

Industry/Entity Type

Restaurant

Requirements
Must have
• Full Name of Restaurant: Brevenna Wine Bar & Restaurant
Address: 812 4th Ave NW, Saltmere, Coastland 00417
Phone: 541.555.0172
website: brevennawinebar.example (do not use www)
Should not have
• Loud colors.

```html
<!DOCTYPE html>
<html lang="en">
<head>
<meta charset="utf-8">
<title>Brevenna Wine Bar &amp; Restaurant — Business Card</title>
<link rel="stylesheet" href="https://fonts.googleapis.com/css2?family=Arimo:wght@400&display=swap">
<style>
  :root {
    --page: #ffffff;
    --card: #ffffff;
    --card-edge: #ececec;
    --green-deep: #566b3c;
    --green-soft: #939f78;
    --green-name: #5e7245;
    --ink: #333333;
  }
  * { box-sizing: border-box; margin: 0; padding: 0; }
  html, body {
    width: 1200px; height: 901px; overflow: hidden;
    background: var(--page);
    font-family: "Arimo", Arial, sans-serif;
  }
  .business-card {
    position: absolute; left: 141px; top: 188px;
    width: 921px; height: 524px;
    background: var(--card);
    border: 1px solid var(--card-edge);
    overflow: hidden;
  }
  .wave-band { position: absolute; left: 0; top: 0; width: 921px; height: 524px; }
  .brand-name {
    position: absolute; left: 43px; width: 462px; top: 186px;
    text-align: center;
    font-size: 68px; line-height: 1; font-weight: 400;
    color: var(--green-name); letter-spacing: 2px;
  }
  .brand-rule {
    position: absolute; left: 43px; top: 281px;
    width: 462px; height: 2px; background: var(--green-soft);
  }
  .brand-tagline {
    position: absolute; left: 43px; width: 462px; top: 294px;
    text-align: center; font-size: 35px; line-height: 1.1; color: var(--ink);
  }
  .contact {
    position: absolute; left: 589px; top: 192px;
    font-style: normal;
    font-size: 24px; line-height: 32px; color: var(--ink);
  }
  .contact-address { margin-bottom: 16px; }
  .contact-line { display: flex; align-items: center; gap: 6px; }
  .contact-icon { width: 18px; height: 18px; flex: none; }
</style>
</head>
<body>
  <article class="business-card">
    <svg class="wave-band" viewBox="0 0 921 524" aria-hidden="true">
      <path fill="var(--green-soft)" d="M0 416 C200 400 400 470 620 488 C760 498 860 440 921 396 L921 524 L0 524 Z"/>
      <path fill="var(--green-deep)" d="M0 456 C200 440 420 490 640 498 C780 502 860 455 921 418 L921 524 L0 524 Z"/>
    </svg>

    <h1 class="brand-name">Brevenna</h1>
    <div class="brand-rule"></div>
    <p class="brand-tagline">Wine Bar &amp; Restaurant</p>

    <address class="contact">
      <div class="contact-address">812 4th Ave NW<br>Saltmere, Coastland 00417</div>
      <div class="contact-line">
        <svg class="contact-icon" viewBox="0 0 24 24" aria-hidden="true">
          <path fill="var(--green-soft)" d="M6.6 10.8c1.4 2.8 3.8 5.1 6.6 6.6l2.2-2.2c.3-.3.7-.4 1-.2 1.1.4 2.3.6 3.6.6.6 0 1 .4 1 1V20c0 .6-.4 1-1 1C10.6 21 3 13.4 3 4c0-.6.4-1 1-1h3.5c.6 0 1 .4 1 1 0 1.3.2 2.5.6 3.6.1.3 0 .7-.2 1l-2.3 2.2z"/>
        </svg>
        <span>541.555.0172</span>
      </div>
      <div class="contact-line">
        <svg class="contact-icon" viewBox="0 0 24 24" aria-hidden="true">
          <circle cx="12" cy="12" r="10" fill="var(--green-soft)"/>
          <g fill="none" stroke="#ffffff" stroke-width="1.3">
            <ellipse cx="12" cy="12" rx="4.5" ry="10"/>
            <line x1="2" y1="12" x2="22" y2="12"/>
            <line x1="12" y1="2" x2="12" y2="22"/>
            <path d="M4 7h16M4 17h16"/>
          </g>
        </svg>
        <span>brevennawinebar.example</span>
      </div>
    </address>
  </article>
</body>
</html>
```